New Business Card Design Project

We require a business card design for Vexalund, a newly established Indian company.
Our focus is on the development, manufacturing, and export of a diverse array of pharmaceutical products on a global scale. The card should convey a professional appearance, as our primary markets are in Africa, China, and Southeast Asian nations.
We envision a two-sided business card, with the reverse side dedicated to a logo set against a solid color or an elegantly designed pattern. The corners should be rounded. We would appreciate seeing both horizontal and vertical design options. We trust the designer to utilize their expertise in creating this design.

The content for the business card is included in the attached Word file.

Target Market(s)

Our primary markets are in Africa, China, and Southeast Asian, Latin America, Maldives, Sri Lanka

Industry/Entity Type

Pharmaceutical Manufacturing and Export

Contact Information for Business Card

Colors

Designer to choose colors to be used in the design.

Requirements
Must have
• The reverse side of the business card features solely the logo along with the tagline, "Remedies of Life."
Should not have
• The logo should not exceed two instances, encompassing both the front and back sides of the card.

```html
<!DOCTYPE html>
<html lang="en">
<head>
<meta charset="utf-8">
<title>Vexalund Business Card</title>
<link href="https://fonts.googleapis.com/css2?family=Poppins:wght@400;500;600;700&display=swap" rel="stylesheet">
<style>
  :root {
    --bg: #c4c4c4;
    --brand-blue: #27a9e1;
    --brand-blue-dark: #1b8fc4;
    --brand-red: #f0604d;
    --ink: #3a3a3a;
    --paper: #ffffff;
  }
  * { margin: 0; padding: 0; box-sizing: border-box; }
  html, body { width: 1200px; height: 802px; overflow: hidden; }
  body {
    background: var(--bg);
    font-family: "Poppins", sans-serif;
    position: relative;
  }
  .card {
    position: absolute;
    top: 251px;
    width: 520px;
    height: 300px;
    border-radius: 22px;
    overflow: hidden;
    box-shadow: 0 10px 24px rgba(0,0,0,0.25);
  }
  .card--front { left: 60px; background: var(--paper); }
  .card--back { left: 620px; background: var(--brand-blue); }

  .front-wave { position: absolute; inset: 0; }
  .corner-tab {
    position: absolute; top: 0; right: 40px;
    width: 38px; height: 46px; background: var(--brand-blue);
  }
  .holder {
    position: absolute; top: 34px; right: 92px; text-align: right;
  }
  .holder-name {
    font-size: 25px; font-weight: 700; color: var(--brand-blue); line-height: 1.1;
  }
  .holder-name .surname { color: var(--brand-red); }
  .holder-role {
    font-size: 12px; color: var(--ink); line-height: 1.35; margin-top: 2px;
  }

  .brand {
    position: absolute; left: 34px; top: 114px;
    display: flex; align-items: center; gap: 10px;
  }
  .brand-dot { width: 16px; height: 16px; border-radius: 50%; background: var(--brand-red); }
  .brand-name { font-size: 34px; font-weight: 600; color: var(--brand-blue); line-height: 1; }

  .contact {
    position: absolute; left: 36px; top: 168px;
    font-size: 12px; color: var(--ink); line-height: 1.5;
  }
  .contact-line { display: flex; align-items: center; gap: 7px; }
  .contact-line svg { width: 11px; height: 11px; flex: none; }
  .contact-gap { height: 4px; }

  .website {
    position: absolute; right: 26px; bottom: 20px;
    display: flex; align-items: center; gap: 6px;
    color: var(--paper); font-size: 12px;
  }
  .website svg { width: 11px; height: 11px; }

  .back-pattern { position: absolute; inset: 0; }
  .back-brand {
    position: absolute; inset: 0;
    display: flex; flex-direction: column; align-items: center; justify-content: center;
    color: var(--paper);
  }
  .back-name { font-size: 58px; font-weight: 600; line-height: 1.05; }
  .back-tagline { font-size: 16px; font-weight: 400; letter-spacing: 1px; margin-top: 6px; }
</style>
</head>
<body>

<section class="card card--front">
  <svg class="front-wave" viewBox="0 0 520 300" preserveAspectRatio="none">
    <path d="M0,286 C200,284 330,250 420,195 C465,167 500,142 520,128 L520,300 L0,300 Z" fill="var(--brand-red)"/>
    <path d="M0,290 C203,288 334,256 424,202 C468,175 502,151 520,139 L520,300 L0,300 Z" fill="var(--paper)"/>
    <path d="M0,293 C206,291 337,260 427,206 C471,179 504,157 520,146 L520,300 L0,300 Z" fill="var(--brand-blue)"/>
  </svg>
  <div class="corner-tab"></div>

  <div class="holder">
    <div class="holder-name">Arjun K. <span class="surname">Sethi</span></div>
    <div class="holder-role">CEO<br>Vexalund</div>
  </div>

  <div class="brand">
    <span class="brand-name">Vexalund</span>
    <span class="brand-dot"></span>
  </div>

  <div class="contact">
    <div>Plot No.14, Kesar Colony</div>
    <div>Station Road, Nandpur</div>
    <div>Pin Code: 441190, Maharashtra, India</div>
    <div class="contact-gap"></div>
    <div class="contact-line">
      <svg viewBox="0 0 24 24"><path fill="var(--brand-red)" d="M6.6 10.8a15 15 0 0 0 6.6 6.6l2.2-2.2c.3-.3.7-.4 1-.2 1.1.4 2.3.6 3.6.6.6 0 1 .4 1 1V20c0 .6-.4 1-1 1A17 17 0 0 1 3 4c0-.6.4-1 1-1h3.5c.6 0 1 .4 1 1 0 1.3.2 2.5.6 3.6.1.3 0 .7-.2 1z"/></svg>
      <span>+919800012345</span>
    </div>
    <div class="contact-line">
      <svg viewBox="0 0 24 24"><path fill="var(--brand-red)" d="M2 5h20v14H2z"/><path fill="none" stroke="#fff" stroke-width="2" d="M3 6l9 7 9-7"/></svg>
      <span>asethi@vexalund.com</span>
    </div>
  </div>

  <div class="website">
    <svg viewBox="0 0 24 24"><circle cx="12" cy="12" r="10" fill="none" stroke="#fff" stroke-width="2.4"/><path d="M2 12h20M12 2c3 3 3 17 0 20M12 2c-3 3-3 17 0 20" fill="none" stroke="#fff" stroke-width="1.8"/></svg>
    <span>www.vexalund.com</span>
  </div>
</section>

<section class="card card--back">
  <svg class="back-pattern" viewBox="0 0 520 300" preserveAspectRatio="none" role="img" aria-label="Repeating diagonal brand pattern in tonal blue">
    <defs>
      <linearGradient id="backTone" x1="0" y1="1" x2="1" y2="0">
        <stop offset="0" stop-color="var(--brand-blue-dark)" stop-opacity="0.6"/>
        <stop offset="0.55" stop-color="var(--brand-blue)" stop-opacity="0"/>
        <stop offset="1" stop-color="#4fbbea" stop-opacity="0.5"/>
      </linearGradient>
    </defs>
    <rect width="520" height="300" fill="var(--brand-blue)"/>
    <rect width="520" height="300" fill="url(#backTone)"/>
  </svg>
  <div class="back-brand">
    <div class="back-name">Vexalund</div>
    <div class="back-tagline">Remedies of Life</div>
  </div>
</section>

</body>
</html>
```